Forensic Document Examiner, looking for contemporary update to my stationery design.

Looking for professional, classy logo design for stationery and business cards. My current stationery and business card is attached.I believe a logo image makes a header section interesting, so an intriguing design of a pen, feathered pen, microscope, magnifying glass, etc., would be appropriate. I have been in the business for over 30 years. I leave ideas to the imagination of the designer.My work involves mainly, the comparison of signatures and handwriting. I also resolve alterations, obliterations, and work as shown on my website: www.documentexaminer.infoThe image produced will be printed on quality white stationery and envelopes. The stationery will be photocopied by my clients, so the images should be reproducible. The business cards may be designed in other than white.

Target Market(s)

Attorneys

Font styles to use
Sans Serif

Colors

Designer to choose colors to be used in the design.

Requirements
Must have
• Image suitable for white stationery and photocopying.
• Classy logo and image; no casual fonts.
Nice to have
• Intriguing, contemporary design incorporating a relevant logo to my work.

```html
<!DOCTYPE html>
<html lang="en">
<head>
<meta charset="utf-8">
<title>Daniel R. Whitlow – Business Card</title>
<link rel="stylesheet" href="https://fonts.googleapis.com/css2?family=Arvo&family=Source+Sans+3:ital,wght@0,400;0,600;1,400&display=swap">
<style>
  :root {
    --backdrop: #e9e6e1;
    --card-navy: #15163a;
    --card-navy-deep: #0e0f2b;
    --gold: #f2cf1f;
    --gold-line: #e2c22a;
    --text-light: #dcdde6;
    --text-white: #f4f4f6;
    --mark-grey: #c9cad3;
  }
  * { box-sizing: border-box; margin: 0; padding: 0; }
  html, body { width: 1125px; height: 1200px; overflow: hidden; }
  body {
    background: var(--backdrop);
    font-family: "Source Sans 3", sans-serif;
    position: relative;
  }
  .card {
    position: absolute;
    left: 162px;
    width: 800px;
    height: 455px;
    border-radius: 22px;
    background: radial-gradient(ellipse at 50% 40%, var(--card-navy) 0%, var(--card-navy-deep) 100%);
    box-shadow: 0 6px 14px rgba(0,0,0,0.35);
  }
  .card-front { top: 95px; }
  .card-back { top: 612px; }
  .card-frame {
    position: absolute;
    inset: 18px;
    border: 2px solid var(--gold-line);
    border-radius: 24px;
  }
  .mark-circle {
    position: absolute;
    border-radius: 50%;
    background: var(--mark-grey);
  }
  .card-front .mark-circle { left: 180px; top: 160px; width: 110px; height: 110px; }
  .front-details { position: absolute; left: 338px; top: 140px; }
  .holder-name {
    font-family: "Arvo", serif;
    color: var(--gold);
    font-size: 29px;
    line-height: 1.1;
  }
  .holder-role {
    color: var(--text-light);
    font-size: 19px;
    margin-top: 4px;
  }
  .contact-list { list-style: none; margin-top: 16px; }
  .contact-list li {
    display: flex; align-items: center; gap: 12px;
    color: var(--text-light);
    font-size: 18px;
    line-height: 24px;
  }
  .contact-list svg { width: 16px; height: 16px; fill: var(--gold); flex: none; }
  .back-lockup {
    position: absolute; left: 0; right: 0; top: 138px;
    display: flex; align-items: center; justify-content: center; gap: 22px;
  }
  .card-back .mark-circle { position: static; width: 100px; height: 100px; flex: none; }
  .lockup-name {
    font-family: "Source Sans 3", sans-serif;
    font-weight: 400;
    color: var(--text-white);
    font-size: 48px;
    letter-spacing: 3px;
    line-height: 1;
    text-transform: uppercase;
  }
  .lockup-role {
    color: var(--gold);
    font-weight: 600;
    font-size: 24px;
    margin-top: 8px;
  }
  .services {
    position: absolute; left: 0; right: 0; top: 360px;
    text-align: center;
    color: var(--text-light);
    font-style: italic;
    font-size: 18px;
    line-height: 24px;
  }
</style>
</head>
<body>
  <section class="card card-front">
    <div class="card-frame"></div>
    <div class="mark-circle" aria-hidden="true"></div>
    <div class="front-details">
      <h1 class="holder-name">Daniel R. Whitlow</h1>
      <p class="holder-role">Forensic document Examiner</p>
      <ul class="contact-list">
        <li><svg viewBox="0 0 24 24"><path d="M6.6 10.8a15.1 15.1 0 0 0 6.6 6.6l2.2-2.2a1 1 0 0 1 1-.25 11.4 11.4 0 0 0 3.6.57 1 1 0 0 1 1 1V20a1 1 0 0 1-1 1A17 17 0 0 1 3 4a1 1 0 0 1 1-1h3.5a1 1 0 0 1 1 1c0 1.25.2 2.45.57 3.57a1 1 0 0 1-.25 1z"/></svg>(555) 210-4471</li>
        <li><svg viewBox="0 0 24 24"><path d="M3 5h18v14H3z M3 6l9 7 9-7" fill="none" stroke="currentColor"/><path d="M2 5h20v14H2zM4 7v1l8 5 8-5V7l-8 5z"/></svg>dwhitlow@quillmarkreview.info</li>
        <li><svg viewBox="0 0 24 24"><path d="M12 2a10 10 0 1 0 0 20 10 10 0 0 0 0-20zm-1 17.9A8 8 0 0 1 4.2 10.2L9 15v1a2 2 0 0 0 2 2zm6.9-2.5A2 2 0 0 0 16 16h-1v-3a1 1 0 0 0-1-1H8v-2h2a1 1 0 0 0 1-1V7h2a2 2 0 0 0 2-2v-.4a8 8 0 0 1 2.9 12.8z"/></svg>www.quillmarkreview.info</li>
        <li><svg viewBox="0 0 24 24"><path d="M12 2a7 7 0 0 0-7 7c0 5.2 7 13 7 13s7-7.8 7-13a7 7 0 0 0-7-7zm0 9.5A2.5 2.5 0 1 1 12 6.5a2.5 2.5 0 0 1 0 5z"/></svg>P.O.Box 4120, Millbrook, OR 97000</li>
      </ul>
    </div>
  </section>

  <section class="card card-back">
    <div class="card-frame"></div>
    <div class="back-lockup">
      <div class="mark-circle" aria-hidden="true"></div>
      <div>
        <p class="lockup-name">Daniel R.<br>Whitlow</p>
        <p class="lockup-role">Forensic Document Examiner</p>
      </div>
    </div>
    <p class="services">Full service laboratory, Specializing in handwriting comparisons,<br>obliterations, alterations indented writing recovery, etc.</p>
  </section>
</body>
</html>
```